Stage Design Company Business Card

We are looking to step up up our business card design for our team.

We are a Full service Design and Consultation company for Stage and TV with an emphasis in Theatrical Lighting.

We like our materials to be clean and modern with solid colors free of patterns and gradients. Our brand consists of 4 primary colors Purple, Black, Grey, and White. Provided is our Word Mark as well as our Symbol Logo.

We would like our cards to leave an impression beyond the information, show our attention to design and detail, and make our marks an easily recognized feature (together or apart) for our clients.

We need a warm approachable comfortable feel for some clients, and a professional flair for the board member type clients.

Attached are our brand elements, and our existing cards to give a sense of our style and a glipse at the information we provide on our cards.

Target Market(s)

broad client base from church leaders to high school teachers and architects.

Industry/Entity Type

Business

Contact Information for Business Card

We format our phone number with periods not parenthesis or dashes. Information will be edited for each of our team members, and team member specific cards are not part of this scope, but rather a template so to speak.

Font styles to use
Sans Serif

Colors
6b449b
ffffff
000000
333333
aaaaaa

Requirements
Must have
• Wordmark and logo mark present (does not need to exist on the same side of card)
• Brand Colors,
• Name, Phone, Email, Address.
• Unique choices that make someone stop and take a second look
Nice to have
• It would be nice to somehow convey what we DO, as our brand name does not lend itself to this, outside of an obvious tagline though.....
• social media if not crowded. all of our handles match (instagram, twitter, facebook)
Should not have
• "clipart"

```html
<!DOCTYPE html>
<html lang="en">
<head>
<meta charset="utf-8">
<title>Marlow Stageworks – Business Card</title>
<link rel="stylesheet" href="https://fonts.googleapis.com/css2?family=Jost:wght@400;500;700&display=swap">
<style>
  :root {
    --purple: #3b2470;
    --black: #111111;
    --ink: #333333;
    --grey: #aaaaaa;
    --white: #ffffff;
    --stage: #8c8b8c;
  }
  * { margin: 0; padding: 0; box-sizing: border-box; }
  html, body { width: 1200px; height: 929px; overflow: hidden; }
  body {
    background: var(--stage);
    font-family: "Jost", sans-serif;
    position: relative;
  }
  .card {
    position: absolute;
    width: 560px;
    height: 320px;
    background: var(--white);
    overflow: hidden;
    box-shadow: 0 6px 14px rgba(0,0,0,0.25);
  }
  .card--front { left: 90px; top: 100px; }
  .card--back { left: 550px; top: 500px; }

  .mark-field {
    position: absolute;
    left: -110px;
    top: 40px;
    width: 260px;
    height: 260px;
    border-radius: 50%;
    background: var(--purple);
  }

  .wordmark { position: absolute; text-align: left; }
  .wordmark__name {
    font-weight: 500;
    font-size: 17px;
    letter-spacing: 0.55em;
    color: var(--black);
  }
  .wordmark__tag {
    font-size: 6px;
    letter-spacing: 0.62em;
    color: var(--grey);
    margin-top: 4px;
  }
  .card--front .wordmark { left: 370px; top: 140px; }
  .card--back .wordmark { right: 40px; top: 40px; }

  .contact {
    position: absolute;
    right: 40px;
    top: 100px;
    text-align: right;
    color: var(--ink);
  }
  .contact__name {
    font-weight: 700;
    font-size: 22px;
    color: var(--purple);
    line-height: 1;
  }
  .contact__role { font-size: 12px; margin-top: 2px; }
  .contact__address { font-size: 13px; margin-top: 18px; line-height: 1.25; }
  .contact__list { list-style: none; margin-top: 12px; font-size: 14px; line-height: 1.45; }
  .contact__list li { display: flex; justify-content: flex-end; align-items: center; gap: 8px; }
  .icon { width: 14px; height: 14px; display: block; }
</style>
</head>
<body>

  <section class="card card--front" aria-label="Card front">
    <div class="mark-field"></div>
    <div class="wordmark">
      <div class="wordmark__name">MARLOW</div>
      <div class="wordmark__tag">STAGEWORKS</div>
    </div>
  </section>

  <section class="card card--back" aria-label="Card back">
    <div class="mark-field"></div>
    <div class="wordmark">
      <div class="wordmark__name">MARLOW</div>
      <div class="wordmark__tag">STAGEWORKS</div>
    </div>
    <div class="contact">
      <div class="contact__name">REID T MARLOW</div>
      <div class="contact__role">OWNER</div>
      <div class="contact__address">52 N. Cedar Ave Tempe,<br>AZ 85281</div>
      <ul class="contact__list">
        <li>800.555.0142
          <svg class="icon" viewBox="0 0 14 14" aria-hidden="true"><rect width="14" height="14" rx="2" fill="var(--purple)"/><path d="M4 3.5l1.6 0 .6 2-1 .8a5 5 0 0 0 2.5 2.5l.8-1 2 .6 0 1.6c-3.5.4-6.9-3-6.5-6.5z" fill="var(--white)"/></svg>
        </li>
        <li>info@marlow-s.com
          <svg class="icon" viewBox="0 0 14 14" aria-hidden="true"><rect width="14" height="14" rx="2" fill="var(--purple)"/><rect x="3" y="4" width="8" height="6" fill="none" stroke="var(--white)" stroke-width="1.2"/><path d="M3 4l4 3.2L11 4" fill="none" stroke="var(--white)" stroke-width="1.2"/></svg>
        </li>
        <li>marlow-s.com
          <svg class="icon" viewBox="0 0 14 14" aria-hidden="true"><rect width="14" height="14" rx="2" fill="var(--purple)"/><circle cx="6" cy="6" r="2.6" fill="none" stroke="var(--white)" stroke-width="1.3"/><path d="M8 8l3 3" stroke="var(--white)" stroke-width="1.5"/></svg>
        </li>
      </ul>
    </div>
  </section>

</body>
</html>
```